Coastline Premier Retreats Business Card Design

Design a business card for Coastline Premier Retreats. Look at the website for colors and reference. Card should have logo, name, title, office number, mobile number, email, URL and a tagline like, "Luxury Hotel & Resort Email Marketing" (This might change).

https://www.coastlinepremierretreats.example

The rest I will leave up to your imagination.

Contact Information for Business Card

Logo, name, title, office number, mobile number, email, URL and a tagline like, "Luxury Hotel & Resort Email Marketing" (This might change).

```html
<!DOCTYPE html>
<html lang="en">
<head>
<meta charset="utf-8">
<title>Coastline Premier Retreats — Business Card</title>
<link rel="stylesheet" href="https://fonts.googleapis.com/css2?family=Montserrat:wght@400;500;700;800&display=swap">
<style>
  :root {
    --bg: #d9d9d9;
    --card-light: #4a4a4a;
    --card-mid: #1a1a1a;
    --card-dark: #070707;
    --orange: #f07a2a;
    --orange-soft: #f59a5a;
    --white: #ffffff;
    --text-muted: #e8e8e8;
  }
  * { box-sizing: border-box; margin: 0; padding: 0; }
  html, body {
    width: 1200px; height: 1200px; overflow: hidden;
    background: var(--bg);
    font-family: "Montserrat", sans-serif;
  }
  .canvas {
    width: 1200px; height: 1200px;
    display: flex; flex-direction: column; align-items: center; justify-content: center;
    gap: 60px;
  }
  .card {
    position: relative;
    width: 840px; height: 480px;
    border-radius: 26px;
    background: linear-gradient(110deg, var(--card-light) 0%, var(--card-mid) 38%, var(--card-dark) 70%);
    box-shadow: 0 10px 24px rgba(0,0,0,0.25);
    overflow: hidden;
    color: var(--white);
  }
  .brand {
    display: flex; align-items: center; gap: 14px;
    font-weight: 800; text-transform: uppercase; color: var(--white);
    letter-spacing: 0.04em; white-space: nowrap;
  }
  .brand-mark { background: var(--orange); flex: none; }

  /* Front */
  .card-front .brand {
    position: absolute; top: 150px; left: 0; right: 0; justify-content: center;
    font-size: 38px;
  }
  .card-front .brand-mark { width: 30px; height: 30px; }
  .divider {
    position: absolute; left: 0; right: 0; top: 330px; height: 2px; background: var(--white);
  }
  .tagline {
    position: absolute; top: 304px; left: 50%; transform: translateX(-50%);
    width: 560px; height: 54px; border-radius: 27px;
    background: linear-gradient(90deg, var(--orange-soft), var(--orange));
    display: flex; align-items: center; justify-content: center;
    font-size: 21px; font-weight: 500; color: var(--white);
  }

  /* Back */
  .card-back .brand {
    position: absolute; top: 58px; right: 48px; font-size: 19px; gap: 10px;
  }
  .card-back .brand-mark { width: 16px; height: 16px; }
  .person { position: absolute; left: 60px; top: 218px; }
  .person-name { font-size: 34px; font-weight: 800; color: var(--orange); line-height: 1.1; }
  .person-title { font-size: 19px; font-weight: 500; margin-top: 4px; color: var(--text-muted); }
  .contacts { list-style: none; margin-top: 18px; }
  .contacts li {
    display: flex; align-items: center; gap: 12px;
    font-size: 19px; font-weight: 500; line-height: 1.55;
  }
  .contacts svg { width: 18px; height: 18px; flex: none; fill: var(--orange); }
  .accent { color: var(--orange); }
  .address {
    position: absolute; right: 48px; top: 300px; text-align: right;
    font-size: 19px; font-weight: 500; line-height: 1.45;
  }
  .address .region { color: var(--orange); }
</style>
</head>
<body>
<main class="canvas">
  <section class="card card-front" aria-label="Card front">
    <div class="brand"><span class="brand-mark"></span>Coastline Premier Retreats</div>
    <div class="divider"></div>
    <div class="tagline">Luxury Hotel &amp; Resort Email Marketing</div>
  </section>

  <section class="card card-back" aria-label="Card back">
    <div class="brand"><span class="brand-mark"></span>Coastline Premier Retreats</div>
    <div class="person">
      <p class="person-name">Daniel Morrow</p>
      <p class="person-title">Founder &amp; Director</p>
      <ul class="contacts">
        <li>
          <svg viewBox="0 0 24 24" aria-hidden="true"><path d="M6.6 10.8a15.1 15.1 0 0 0 6.6 6.6l2.2-2.2c.3-.3.7-.4 1-.2 1.1.4 2.3.6 3.6.6.6 0 1 .4 1 1V20c0 .6-.4 1-1 1A17 17 0 0 1 3 4c0-.6.4-1 1-1h3.5c.6 0 1 .4 1 1 0 1.3.2 2.5.6 3.6.1.3 0 .7-.2 1z"/></svg>
          555.214.7300
        </li>
        <li>
          <svg viewBox="0 0 24 24" aria-hidden="true"><path d="M7 1h10a2 2 0 0 1 2 2v18a2 2 0 0 1-2 2H7a2 2 0 0 1-2-2V3a2 2 0 0 1 2-2zm0 3v14h10V4zm5 15.5a1 1 0 1 0 0 2 1 1 0 0 0 0-2z"/></svg>
          555-390-4127
        </li>
        <li>
          <svg viewBox="0 0 24 24" aria-hidden="true"><path d="M2 5h20v14H2zm2 2v.4l8 5 8-5V7zm0 2.7V17h16V9.7l-8 5z"/></svg>
          info@coastlinepremierretreats.example
        </li>
        <li>
          <svg viewBox="0 0 24 24" aria-hidden="true"><path d="M12 2a10 10 0 1 0 0 20 10 10 0 0 0 0-20zm6.9 9h-3a15 15 0 0 0-1.3-5.6A8 8 0 0 1 18.9 11zM12 4.1c.9 1.3 1.7 3.6 1.9 6.9h-3.8c.2-3.3 1-5.6 1.9-6.9zM9.4 5.4A15 15 0 0 0 8.1 11h-3a8 8 0 0 1 4.3-5.6zM5.1 13h3a15 15 0 0 0 1.3 5.6A8 8 0 0 1 5.1 13zm6.9 6.9c-.9-1.3-1.7-3.6-1.9-6.9h3.8c-.2 3.3-1 5.6-1.9 6.9zm2.6-1.3a15 15 0 0 0 1.3-5.6h3a8 8 0 0 1-4.3 5.6z"/></svg>
          <span>www.<span class="accent">coastlinepremierretreats</span>.example</span>
        </li>
      </ul>
    </div>
    <address class="address" style="font-style: normal;">
      <span class="region">North America,</span><br>
      4170 Harbor Lane<br>
      Bayview Maine 04012
    </address>
  </section>
</main>
</body>
</html>
```